We need a card and logo design for a new business based in Dallas Texas called Stonemarsh Financial LLC.

We provide bridge loans.We offer pay day loans,title loans and check cashing.Our products are emmergency loans that help borrowers meet short term liquidity needs until the next pay check.

The final design should communicate,professionalism,Sophistication and friendliness to our customers.Use the color Blue as much as possible and another eye catching color if possible.We will consider a profesional looking knight logo with the color Blue in it.Please design a full corporate identity.

```html
<!DOCTYPE html>
<html lang="en">
<head>
<meta charset="utf-8">
<title>Stonemarsh Financial LLC – Business Card</title>
<link rel="stylesheet" href="https://fonts.googleapis.com/css2?family=Open+Sans:wght@300;400;700&family=Montserrat:wght@700&display=swap">
<style>
  :root {
    --backdrop: #2e2e2e;
    --card-white: #ffffff;
    --band-grey: #7b7b7b;
    --brand-blue: #2b93d8;
    --ink-grey: #555555;
    --ink-light: #f2f2f2;
  }
  * { margin: 0; padding: 0; box-sizing: border-box; }
  html, body {
    width: 1200px;
    height: 720px;
    overflow: hidden;
    background: var(--backdrop);
  }
  .business-card {
    position: absolute;
    left: 75px;
    top: 60px;
    width: 1050px;
    height: 600px;
    background: var(--card-white);
    overflow: hidden;
    font-family: "Open Sans", Arial, sans-serif;
  }
  .card-shapes {
    position: absolute;
    inset: 0;
    width: 100%;
    height: 100%;
  }
  .brand-block {
    position: absolute;
    left: 90px;
    top: 275px;
    width: 340px;
    display: flex;
    flex-direction: column;
    align-items: center;
    gap: 16px;
  }
  .brand-dot {
    width: 56px;
    height: 56px;
    border-radius: 50%;
    background: var(--brand-blue);
  }
  .brand-name {
    font-family: "Montserrat", Arial, sans-serif;
    font-weight: 700;
    font-size: 16px;
    letter-spacing: 0.3px;
    color: var(--brand-blue);
    text-transform: uppercase;
    white-space: nowrap;
  }
  .holder {
    position: absolute;
    right: 150px;
    top: 178px;
    white-space: nowrap;
  }
  .holder-name {
    font-weight: 300;
    font-size: 30px;
    color: var(--ink-grey);
    text-transform: uppercase;
  }
  .holder-role {
    font-weight: 400;
    font-size: 20px;
    color: var(--brand-blue);
    margin-left: 4px;
  }
  .contact {
    position: absolute;
    right: 65px;
    color: var(--ink-light);
    font-size: 22px;
    line-height: 1.3;
    text-align: left;
  }
  .contact-phones { top: 385px; }
  .contact-web { top: 487px; }
</style>
</head>
<body>
  <div class="business-card">
    <svg class="card-shapes" viewBox="0 0 1050 600" preserveAspectRatio="none" aria-hidden="true">
      <rect class="grey-band" x="0" y="0" width="1050" height="600" fill="var(--band-grey)"/>
      <path class="left-arc" d="M0,0 L130,0 C330,70 470,320 495,600 L0,600 Z" fill="var(--card-white)"/>
      <path class="right-arc" d="M430,0 C520,220 780,350 1050,360 L1050,0 Z" fill="var(--card-white)"/>
    </svg>

    <div class="brand-block">
      <span class="brand-dot"></span>
      <span class="brand-name">Stonemarsh Financial LLC</span>
    </div>

    <div class="holder">
      <span class="holder-name">Evan Hale</span><span class="holder-role">manager</span>
    </div>

    <div class="contact contact-phones">
      <p>+ 000 - 2468 - 1357</p>
      <p>+ 000 - 8642 - 9753</p>
    </div>

    <div class="contact contact-web">
      <p>admin@stonemarsh.net</p>
      <p>StonemarshFinancial.com</p>
    </div>
  </div>
</body>
</html>
```